Bright Path Notes Wordpress Blog

I need to design a WordPress blog page. The name of the Blog is "Bright Path Notes". I am hoping for a simple design that is easy for me to post future posts to. I like the color teal for this. The website is brightpathnotesblog.com where I am going to write a personal blog. I don't have a logo for this, but am hoping for a header that has some swirly, but classy looking text. Easy on the eyes. The website will only have a couple of pages - the home landing page, and an about me page.

Font styles to use
Script

Colors
00a990
86cfc6
cfeae6

Requirements
Must have
• A header for the landing page of the blog. Clean layout of where the blog posts will lie.

```html
<!DOCTYPE html>
<html lang="en">
<head>
<meta charset="utf-8">
<title>Bright Path Notes</title>
<link href="https://fonts.googleapis.com/css2?family=Roboto+Slab:wght@300;400&family=Open+Sans:wght@400;600&display=swap" rel="stylesheet">
<style>
:root{
  --teal:#1b97a3;
  --teal-light:#5cc3c7;
  --teal-soft:#86cfc6;
  --ink:#333a40;
  --muted:#7b8288;
  --page:#f5f6f8;
  --card:#ffffff;
  --line:#e3e6ea;
  --footer:#2a2a2a;
}
*{box-sizing:border-box;margin:0;padding:0}
html,body{width:1200px;height:2951px;overflow:hidden}
body{background:var(--page);font-family:"Open Sans",Arial,sans-serif;color:var(--ink);position:relative}
.abs{position:absolute}

/* hero */
.hero{left:0;top:0;width:1200px;height:600px;overflow:hidden}
.hero-photo{position:absolute;inset:0;background:
  linear-gradient(180deg,#f4f3ef 0%,#eeece6 38%,#e4dccb 62%,#c9a86a 80%,#b48a45 100%)}
.hero-wave{position:absolute;left:0;bottom:0}
.brand{left:87px;top:120px;display:flex;align-items:center;gap:10px}
.brand-dot{width:56px;height:56px;border-radius:50%;border:3px solid var(--teal)}
.brand-name{font-family:"Roboto Slab",Georgia,serif;font-weight:400;font-size:26px;color:var(--teal)}
.nav{left:672px;top:142px;display:flex;font-size:11px;font-weight:600;color:#333}
.nav a{color:#333;text-decoration:none;width:100px;text-align:left}
.search{left:1066px;top:125px;width:48px;height:48px;border:1.5px solid var(--teal-light);border-radius:50%}
.search svg{position:absolute;left:15px;top:15px}
.hero-title{left:87px;top:212px;font-family:"Roboto Slab",Georgia,serif;font-weight:400;font-size:36px;color:var(--teal);letter-spacing:1px}
.hero-text{left:87px;top:275px;width:500px;font-size:11.5px;line-height:25px;color:#666}
.btn{left:87px;top:363px;width:118px;height:38px;background:var(--teal);color:#fff;font-size:14px;line-height:38px;text-align:center;border-radius:3px}
.dots{left:574px;top:520px;display:flex;gap:4px}
.dots span{width:14px;height:14px;border-radius:50%;border:2px solid #6a7f80}
.dots span.on{border-color:var(--teal-light);background:rgba(92,195,199,.3)}

/* section headings */
.h2{font-family:"Roboto Slab",Georgia,serif;font-weight:400;font-size:23px;color:#333}
.h2 em{font-style:normal;color:var(--teal-light)}
.intro{left:87px;top:730px;width:680px;font-size:11.5px;line-height:25px;color:#777}

/* posts */
.post{left:87px;width:680px;height:315px;background:var(--card);border:1px solid var(--line)}
.post-img{position:absolute;left:19px;top:26px;width:224px;height:200px}
.post-title{position:absolute;left:261px;top:28px;font-family:"Roboto Slab",Georgia,serif;font-weight:400;font-size:17px;color:#333}
.post-meta{position:absolute;left:261px;top:66px;font-size:10.5px;color:var(--teal-light);text-decoration:underline;font-style:italic}
.post-meta b{font-weight:400;color:#999;margin:0 8px;display:inline-block;font-style:normal}
.post-text{position:absolute;left:261px;top:98px;width:390px;font-size:11.5px;line-height:25px;color:#777}
.post-bar{position:absolute;left:0;right:0;bottom:0;height:45px;border-top:1px solid var(--line);display:flex}
.post-bar i{width:79px;border-right:1px solid var(--line);display:flex;align-items:center;justify-content:center}
.post-bar i::before{content:"";width:9px;height:9px;border-radius:50%;background:#444}
.post-bar .more{flex:1;font-size:11px;color:var(--teal-light);text-decoration:underline;display:flex;align-items:center;justify-content:center}

/* sidebar */
.about-text{left:806px;top:724px;width:310px;font-size:11.5px;line-height:25px;color:#666}
.avatar{left:806px;top:890px;width:76px;height:76px;border-radius:50%;background:linear-gradient(135deg,#8a6a52,#d9b99a);border:3px solid #fff;box-shadow:0 0 0 1px var(--line)}
.name{left:900px;top:910px;font-size:12px;color:var(--teal-light);font-weight:600}
.posted{left:900px;top:932px;font-size:11px;color:#777}
.divider{left:806px;top:1003px;width:310px;height:1px;background:var(--line)}
.pop{left:806px;width:310px;height:86px}
.pop p{width:210px;font-size:10.5px;line-height:20px;color:#666}
.pop .meta{font-size:9.5px;color:var(--teal-light);text-decoration:underline;font-style:italic;margin-top:4px}
.pop .thumb{position:absolute;left:223px;top:0;width:86px;height:83px}

.feed{left:806px;top:1442px;width:310px;height:402px}
.tab{position:absolute;top:0;height:36px;color:#fff;font-size:15px;font-weight:600;line-height:36px;text-align:center}
.tab-a{left:0;width:124px;background:#55acdc}
.tab-b{left:130px;width:128px;background:#3b5998}
.feed-box{position:absolute;left:0;top:36px;width:310px;height:366px;background:#55acdc;padding:10px}
.feed-inner{background:#fff;height:346px;overflow:hidden;position:relative}
.feed-head{padding:10px;font-size:12.5px;color:var(--teal);border-bottom:1px solid var(--line)}
.tweet{padding:8px 12px;border-bottom:1px solid var(--line);font-size:10.5px;color:#666}
.tweet .row{display:flex;gap:12px;margin:10px 0}
.tweet .ico{width:44px;height:44px;border:1px solid var(--line);display:flex;align-items:center;justify-content:center}
.tweet .ico::before{content:"";width:22px;height:22px;border-radius:4px;background:#55acdc}
.tweet small{font-size:9.5px;color:#888;line-height:18px;display:block}
.scroll{position:absolute;right:2px;top:70px;width:6px;height:100px;background:#c7c7c7;border-radius:3px}

/* newsletter */
.news{left:0;top:2610px;width:1200px;height:105px;background:var(--teal)}
.news h3{position:absolute;left:115px;top:30px;font-family:"Roboto Slab",Georgia,serif;font-weight:300;font-size:31px;color:#fff}
.news .field{position:absolute;left:423px;top:34px;width:505px;height:38px;background:#fff;border-radius:3px;font-size:11px;color:#666;line-height:38px;padding-left:16px}
.news .sub{position:absolute;left:936px;top:34px;width:148px;height:38px;background:var(--teal-soft);color:#fff;font-size:15px;line-height:38px;text-align:center;border-radius:3px;letter-spacing:.5px}

/* footer */
.footer{left:0;top:2715px;width:1200px;height:236px;background:var(--footer)}
.soc{position:absolute;top:32px;display:flex;gap:12px;left:390px}
.soc span{width:60px;height:60px;border:1.5px solid #aaa;border-radius:50%;display:flex;align-items:center;justify-content:center}
.soc span::before{content:"";width:10px;height:10px;border-radius:50%;background:#ddd}
.foot-line{position:absolute;left:87px;top:108px;width:1028px;height:1px;background:#444}
.foot-nav{position:absolute;top:134px;left:0;width:1200px;display:flex;justify-content:center;gap:40px;font-size:11.5px;color:#ccc}
.foot-nav span.sep{color:#888}
.copy{position:absolute;top:177px;width:1200px;text-align:center;font-size:11px;color:#ccc}
</style>
</head>
<body>

<header class="abs hero">
  <div class="hero-photo" role="img" aria-label="Photo of a woman with raised arms in a sunlit golden wheat field"></div>
  <svg class="hero-wave" width="1200" height="90" viewBox="0 0 1200 90">
    <path d="M0 90 L0 70 C250 90 500 30 760 30 C950 30 1100 50 1200 70 L1200 90 Z" fill="#f5f6f8"/>
    <path d="M0 70 C250 90 500 30 760 30 C950 30 1100 50 1200 70" fill="none" stroke="#5cc3c7" stroke-width="3"/>
  </svg>
</header>

<div class="abs brand"><span class="brand-dot"></span><span class="brand-name">Bright Path Notes</span></div>
<nav class="abs nav"><a>HOME</a><a>ABOUT</a><a>BLOG</a><a>CONTACT US</a></nav>
<div class="abs search"><svg width="16" height="16" viewBox="0 0 16 16"><circle cx="6.5" cy="6.5" r="4.5" fill="none" stroke="#5cc3c7" stroke-width="2"/><line x1="10" y1="10" x2="14" y2="14" stroke="#5cc3c7" stroke-width="2"/></svg></div>
<h1 class="abs hero-title">BRIGHT PATH NOTES</h1>
<p class="abs hero-text">Sed ut perspiciatis unde omnis iste natus error sit voluptatem accusantium doloremque laudantium, totam rem aperiam, eaque ipsa quae ab illo inventore veritatis et quasi archit ecto beatae vitae dicta sunt ratione voluptatem sequi nesciunt.</p>
<div class="abs btn">READ MORE</div>
<div class="abs dots"><span></span><span class="on"></span><span></span></div>

<h2 class="abs h2" style="left:87px;top:678px">Welcome to <em>Bright Path Notes</em></h2>
<p class="abs intro">Sed ut perspiciatis unde omnis iste natus error sit voluptatem accusantium doloremque laudantium, totam rem aperiam, eaque ipsa are quae ab illo inventore veritatis et quasi architecto beatae vitae dicta sunt explicabo.</p>

<article class="abs post" style="top:797px">
  <div class="post-img" role="img" aria-label="Photo of a woman blowing a dandelion in a meadow" style="background:linear-gradient(135deg,#5f7d3a,#a9c46c 60%,#d8e2b0)"></div>
  <h3 class="post-title">Neque porro quisquam est qui dolorem ipsum</h3>
  <div class="post-meta">Alex Reed<b>|</b>20 Mar 2017<b>|</b>Comments (05)</div>
  <p class="post-text">Sed ut perspiciatis unde omnis iste natus error sit voluptatem accusan tium dol remque laudantium, totam rem aperiam, eaque ipsa are quae ab illo inv entore veritatis et quasi architecto beatae vitae dicta sunt ex plicabo. dolores eos qui ratione voluptatem sequi nesciunt.tium dol tot am rem aperiam, eaque ipsa are quae</p>
  <div class="post-bar"><i></i><i></i><i></i><i></i><i></i><i></i><i></i><span class="more">READ MORE</span></div>
</article>

<article class="abs post" style="top:1141px">
  <div class="post-img" role="img" aria-label="Photo of a mother lifting her child outdoors in bright light" style="background:linear-gradient(135deg,#f3efe6,#d9d2c2 55%,#a8b494)"></div>
  <h3 class="post-title">Neque porro quisquam est qui dolorem ipsum</h3>
  <div class="post-meta">Alex Reed<b>|</b>20 Mar 2017<b>|</b>Comments (05)</div>
  <p class="post-text">Sed ut perspiciatis unde omnis iste natus error sit voluptatem accusan tium dol remque laudantium, totam rem aperiam, eaque ipsa are quae ab illo inv entore veritatis et quasi architecto beatae vitae dicta sunt ex plicabo. dolores eos qui ratione voluptatem sequi nesciunt.tium dol tot am rem aperiam, eaque ipsa are quae</p>
  <div class="post-bar"><i></i><i></i><i></i><i></i><i></i><i></i><i></i><span class="more">READ MORE</span></div>
</article>

<article class="abs post" style="top:1487px">
  <div class="post-img" role="img" aria-label="Photo of a family walking together in a sunny park" style="background:linear-gradient(180deg,#b9d3e6,#e8ecd8 50%,#7e9a4c)"></div>
  <h3 class="post-title">Neque porro quisquam est qui dolorem ipsum</h3>
  <div class="post-meta">Alex Reed<b>|</b>20 Mar 2017<b>|</b>Comments (05)</div>
  <p class="post-text">Sed ut perspiciatis unde omnis iste natus error sit voluptatem accusan tium dol remque laudantium, totam rem aperiam, eaque ipsa are quae ab illo inv entore veritatis et quasi architecto beatae vitae dicta sunt ex plicabo. dolores eos qui ratione voluptatem sequi nesciunt.tium dol tot am rem aperiam, eaque ipsa are quae</p>
  <div class="post-bar"><i></i><i></i><i></i><i></i><i></i><i></i><i></i><span class="more">READ MORE</span></div>
</article>

<article class="abs post" style="top:1831px">
  <div class="post-img" role="img" aria-label="Photo of two friends laughing among autumn trees" style="background:linear-gradient(135deg,#6c5a2a,#c9a03c 55%,#e8d27a)"></div>
  <h3 class="post-title">Neque porro quisquam est qui dolorem ipsum</h3>
  <div class="post-meta">Alex Reed<b>|</b>20 Mar 2017<b>|</b>Comments (05)</div>
  <p class="post-text">Sed ut perspiciatis unde omnis iste natus error sit voluptatem accusan tium dol remque laudantium, totam rem aperiam, eaque ipsa are quae ab illo inv entore veritatis et quasi architecto beatae vitae dicta sunt ex plicabo. dolores eos qui ratione voluptatem sequi nesciunt.tium dol tot am rem aperiam, eaque ipsa are quae</p>
  <div class="post-bar"><i></i><i></i><i></i><i></i><i></i><i></i><i></i><span class="more">READ MORE</span></div>
</article>

<article class="abs post" style="top:2168px">
  <div class="post-img" role="img" aria-label="Photo of a family running with a kite in a golden field" style="background:linear-gradient(180deg,#f2e6c8,#d6b478 55%,#8a6a34)"></div>
  <h3 class="post-title">Neque porro quisquam est qui dolorem ipsum</h3>
  <div class="post-meta">Alex Reed<b>|</b>20 Mar 2017<b>|</b>Comments (05)</div>
  <p class="post-text">Sed ut perspiciatis unde omnis iste natus error sit voluptatem accusan tium dol remque laudantium, totam rem aperiam, eaque ipsa are quae ab illo inv entore veritatis et quasi architecto beatae vitae dicta sunt ex plicabo. dolores eos qui ratione voluptatem sequi nesciunt.tium dol tot am rem aperiam, eaque ipsa are quae</p>
  <div class="post-bar"><i></i><i></i><i></i><i></i><i></i><i></i><i></i><span class="more">READ MORE</span></div>
</article>

<aside>
  <h2 class="abs h2" style="left:806px;top:678px">About <em>Maya</em></h2>
  <p class="abs about-text"><span style="color:#999;font-size:16px">&ldquo;</span> Sed ut perspiciatis unde omnis iste natus error sit volup atem accusantium doloremque laudantium, totam rem aperiam, eaque ipsa are quae ab illo inventore verit atis et quasi architecto beatae vitae dicta sunt explicabo. eni ipsam voluptatem quia aut fugit, sed quia consequ ratione voluptatem sequi nesciunt.</p>
  <div class="abs avatar" role="img" aria-label="Portrait photo of the blog author"></div>
  <div class="abs name">NAME : MAYA</div>
  <div class="abs posted">Posted on 17 Mar 2017</div>
  <div class="abs divider"></div>

  <h2 class="abs h2" style="left:806px;top:1022px">Most <em>Popular</em></h2>
  <div class="abs pop" style="top:1070px">
    <p>Sed ut perspiciatis unde omnis iste nat us error sit voluptatem accusantium dol oremque laudantium</p>
    <div class="meta">20 Mar 2017 &nbsp;|&nbsp; Comments (05)</div>
    <div class="thumb" role="img" aria-label="Photo of friends taking a selfie" style="background:linear-gradient(135deg,#5a3a2a,#b07850)"></div>
  </div>
  <div class="abs pop" style="top:1190px">
    <p>Sed ut perspiciatis unde omnis iste nat us error sit voluptatem accusantium dol oremque laudantium</p>
    <div class="meta">20 Mar 2017 &nbsp;|&nbsp; Comments (05)</div>
    <div class="thumb" role="img" aria-label="Photo of two women smiling together" style="background:linear-gradient(135deg,#8a4a4a,#d79a88)"></div>
  </div>
  <div class="abs pop" style="top:1310px">
    <p>Sed ut perspiciatis unde omnis iste nat us error sit voluptatem accusantium dol oremque laudantium</p>
    <div class="meta">20 Mar 2017 &nbsp;|&nbsp; Comments (05)</div>
    <div class="thumb" role="img" aria-label="Photo of a sunset over a green field" style="background:linear-gradient(180deg,#e79a4a,#f2c872 50%,#7ea048)"></div>
  </div>

  <div class="abs feed">
    <div class="tab tab-a">Tweets</div>
    <div class="tab tab-b">Updates</div>
    <div class="feed-box"><div class="feed-inner">
      <div class="feed-head">Tweets by @brightpathnotesblog.com/</div>
      <div class="tweet">brightpathnotes @ Lorem Ipsum
        <div class="row"><span class="ico"></span><small>Lorem Ipsum Dummy Text<br>@ brightpathnotes Dec 13 2017</small></div>
        Sed ut perspiciatis unde omnis iste voluptatem santium doloremque....</div>
      <div class="tweet" style="border:0">brightpathnotes @ Lorem Ipsum
        <div class="row"><span class="ico"></span><small>Lorem Ipsum Dummy Text<br>@ brightpathnotes Dec 13 2017</small></div>
        Sed ut perspiciatis unde omnis iste voluptatem santium doloremque....</div>
      <span class="scroll"></span>
    </div></div>
  </div>
</aside>

<section class="abs news">
  <h3>Newsletter Signup :</h3>
  <div class="field">Enter Your Email Id :</div>
  <div class="sub">SUBSCRIBE</div>
</section>

<footer class="abs footer">
  <div class="soc"><span></span><span></span><span></span><span></span><span></span><span></span></div>
  <div class="foot-line"></div>
  <div class="foot-nav"><span>HOME</span><span class="sep">|</span><span>ABOUT ME</span><span class="sep">|</span><span>BLOG</span><span class="sep">|</span><span>CONTACT US</span></div>
  <div class="copy">&copy; Copyrights 2017 Bright Path Notes.All Rights Reserved.</div>
</footer>

</body>
</html>
```